Fitness Equipment & Service

I want to make the card eye catching and fun. We are called Corvane Motion Limited and we are based in Wales. We sell, install and service all types of fitness equipment from Skipping ropes, right through the Dumbbells, Kettle bells and Barbells through to state of the art Treadmills, Running Machines and Strength Equipment. We also design and install changing room furniture and lockers.

TYPOGRAPHY
We would like to use Futrura. Futura has an appearance of efficiency and forwardness. The typeface is derived
from simple geometric forms (near-perfect circles, triangles and squares) and is based on strokes of
near-even weight, which are low in contrast. This is most visible in the almost perfectly round stroke of
the o, which is nonetheless slightly ovoid.
The lowercase has tall ascenders, which rise above the cap line. The uppercase
characters present proportions similar to those of classical Roman capitals.

TYPOGRAPHIC CONSIDERATIONS
No Strike though
No Horizontal Scaling
No Drop Shadows
No Effects
Never use less than 120% Leading

OUR CORPORATE COLOURS
BRAND GUIDELINES
We were thinking that our primary colour palette consists of the Acid Green (Pantone 382) and Process Black.

We work closely with tquarly Ltd and would like to include their name on the card somewhere. I have attached images of the other brands that we work with as an idea or the small icons I have included that illustrate what we do?. I have very kindly been given permission to use any of the images off the files that I have included below, so I hope these help. I will include these below. I would be open to suggestions if it made the card more striking Can you do it?
Updates

Hi All, Just wanted to add a few thoughts but you are the guys with the creative visions (thats why are here) We are based in Wales, UK and we would be open to lots of different ideas on a theme but must be eye catching, Bold and FUN. If you can or think that the Welsh or any dragon could be put in there then go for it (its not a must have) We have also added some ideas for colour but again its over to you!! GO FOR IT ! Thanks and look forward to your visions! Owen

Hi All, Just thought I would sen through the contact details that need to be on the card. (if you want to play around with icons instead of the wording twitter, Facebook, go for it): Corvane Motion Limited Owen Pritchard Managing Director Mob: +44 (0)7582 913 406 e-mail: sales@corvanemotion.co.uk Web: Corvanemotion.co.uk twitter: @motionLetterbin Facebook: Corvane Motion Limited

```html
<!DOCTYPE html>
<html lang="en">
<head>
<meta charset="utf-8">
<title>Corvane Motion Limited – Business Card</title>
<link rel="stylesheet" href="https://fonts.googleapis.com/css2?family=Arimo:wght@400;700&display=swap">
<style>
  :root {
    --navy-deep: #0f2350;
    --navy: #1b3a7a;
    --navy-light: #2c56a3;
    --gold: #c9a13b;
    --gold-light: #e3c46b;
    --white: #ffffff;
    --paper: #e9e7e2;
    --ink: #15244f;
  }
  * { box-sizing: border-box; margin: 0; padding: 0; }
  html, body { width: 1200px; height: 950px; overflow: hidden; }
  body {
    background: var(--paper);
    font-family: "Arimo", Arial, sans-serif;
    position: relative;
  }
  .card {
    position: absolute;
    left: 250px;
    width: 700px;
    height: 400px;
    border-radius: 4px;
    overflow: hidden;
    box-shadow: 0 6px 18px rgba(0,0,0,.18);
  }

  /* Back of card */
  .card-back {
    top: 50px;
    background: linear-gradient(90deg, var(--navy) 0%, var(--navy-light) 45%, var(--navy) 80%, var(--navy-deep) 100%);
  }
  .card-back .edge-sheen {
    position: absolute; top: 0; right: 0; width: 180px; height: 100%;
    background: linear-gradient(90deg, rgba(255,255,255,0) 0%, rgba(255,255,255,.08) 40%, rgba(15,35,80,.35) 100%);
  }
  .back-mark {
    position: absolute; left: 0; right: 0; top: 110px;
    display: flex; flex-direction: column; align-items: center; gap: 18px;
  }
  .mark-disc {
    width: 110px; height: 110px; border-radius: 50%;
    background: radial-gradient(circle at 40% 35%, var(--navy-light), var(--navy-deep));
    border: 4px solid #b9c3d8;
  }
  .back-name {
    color: var(--white); font-size: 20px; font-weight: 700;
    letter-spacing: 2px; text-transform: uppercase; line-height: 1.3;
  }
  .back-web {
    position: absolute; left: 0; right: 0; bottom: 70px;
    text-align: center; color: var(--white); font-size: 15px;
    letter-spacing: 2px; line-height: 1.3;
  }

  /* Front of card */
  .card-front { top: 500px; background: var(--white); }
  .front-waves { position: absolute; inset: 0; }
  .brand {
    position: absolute; left: 56px; top: 36px;
    display: flex; flex-direction: column; align-items: flex-start; gap: 12px;
  }
  .brand .mark-disc { width: 100px; height: 100px; }
  .brand-name {
    color: var(--ink); font-size: 15px; font-weight: 700;
    letter-spacing: 1px; text-transform: uppercase; line-height: 1.3;
  }
  .person {
    position: absolute; right: 56px; top: 108px; text-align: right; line-height: 1.25;
  }
  .person-name { color: var(--ink); font-size: 24px; font-weight: 700; }
  .person-role { color: var(--gold); font-size: 19px; }
  .contact {
    position: absolute; right: 40px; top: 268px;
    list-style: none; color: var(--white); font-size: 15px; line-height: 1.4;
  }
  .contact li { display: flex; justify-content: flex-end; align-items: center; gap: 10px; height: 21px; }
  .contact .icon { width: 16px; height: 16px; flex: none; }
  .contact .icon-space { width: 16px; flex: none; }
  .social { display: flex; gap: 4px; }
  .social span { width: 13px; height: 13px; background: var(--white); border-radius: 2px; display: block; }
</style>
</head>
<body>

<section class="card card-back">
  <div class="edge-sheen"></div>
  <div class="back-mark">
    <div class="mark-disc"></div>
    <div class="back-name">Corvane Motion Limited</div>
  </div>
  <p class="back-web">corvanemotion.co.uk</p>
</section>

<section class="card card-front">
  <svg class="front-waves" viewBox="0 0 700 400" width="700" height="400" aria-hidden="true">
    <defs>
      <linearGradient id="goldBand" x1="0" x2="1">
        <stop offset="0" stop-color="#a8842c"/>
        <stop offset=".5" stop-color="#e3c46b"/>
        <stop offset="1" stop-color="#b8922f"/>
      </linearGradient>
      <linearGradient id="navyField" x1="0" y1="0" x2="0" y2="1">
        <stop offset="0" stop-color="#2c56a3"/>
        <stop offset="1" stop-color="#15306a"/>
      </linearGradient>
    </defs>
    <path d="M0,238 C120,226 260,268 420,246 C540,230 630,212 700,210 L700,224 C630,226 540,246 420,262 C260,284 120,250 0,254 Z" fill="url(#goldBand)"/>
    <path d="M0,268 C120,260 260,292 420,272 C540,256 630,238 700,234 L700,240 C630,244 540,264 420,280 C260,300 120,268 0,276 Z" fill="#1b3a7a"/>
    <path d="M0,284 C120,276 260,306 420,288 C540,272 630,252 700,248 L700,400 L0,400 Z" fill="url(#navyField)"/>
  </svg>

  <div class="brand">
    <div class="mark-disc"></div>
    <div class="brand-name">Corvane Motion Limited</div>
  </div>

  <div class="person">
    <p class="person-name">Owen Pritchard</p>
    <p class="person-role">Managing Director</p>
  </div>

  <ul class="contact">
    <li>27 Harbour Row <span class="social"><span></span><span></span></span></li>
    <li>Cardiff, CF10 4PL <span class="icon-space"></span></li>
    <li>+44 (0)7582 913 406
      <svg class="icon" viewBox="0 0 16 16" aria-hidden="true"><rect x="4" y="1" width="8" height="14" rx="1.5" fill="none" stroke="#fff" stroke-width="1.6"/><circle cx="8" cy="12.5" r="1" fill="#fff"/></svg>
    </li>
    <li>sales@corvanemotion.co.uk
      <svg class="icon" viewBox="0 0 16 16" aria-hidden="true"><rect x="1" y="3" width="14" height="10" fill="#fff"/><path d="M1,3 L8,9 L15,3" fill="none" stroke="#1b3a7a" stroke-width="1.3"/></svg>
    </li>
    <li>Corvanemotion.co.uk
      <svg class="icon" viewBox="0 0 16 16" aria-hidden="true"><circle cx="8" cy="8" r="7" fill="#fff"/><path d="M4,8 H12 M8,1 C5,5 5,11 8,15 M8,1 C11,5 11,11 8,15" fill="none" stroke="#1b3a7a" stroke-width="1"/></svg>
    </li>
  </ul>
</section>

</body>
</html>
```